Quillfern Vaults - Direct Mailer / Flyer

We are excited to announce the launch of our new company, Quillfern Vaults, a premier cohosting facility and data center dedicated to Cryptocurrency Miners. Our website, https://quillfernvaults.example, provides detailed information about our offerings and showcases the innovative design schemes for the entire project.

Quillfern Vaults stands out in the industry by offering both GPU Hosting and ASIC Hosting services in our state-of-the-art facility, equipped with an impressive 17 Megawatts of available power. What sets us apart is our unique billing system based on actual metered power usage. We charge $0.08 for ASIC miners and $0.09 for GPU miners, ensuring cost-effectiveness and transparency for our clients.

Our commitment to excellence is evident in our use of cutting-edge technology, top-notch facilities, and strategic partnerships. These elements come together to deliver exceptional solutions tailored for real-world applications in the cryptocurrency space.

As part of our promotional efforts, we are developing a direct mailer/flyer to introduce Quillfern Vaults to a wider audience. This promotional material will also serve as a handout at events, to potential customers, and more. We welcome creative ideas and suggestions to maximize the versatility of this design and reach diverse target audiences effectively.

For a comprehensive overview of our services and to explore our design concepts, please visit https://quillfernvaults.example. Quillfern Vaults is poised to revolutionize the mining industry, and we look forward to partnering with you for success in the digital currency era.

```html
<!DOCTYPE html>
<html lang="en">
<head>
<meta charset="utf-8">
<title>Quillfern Vaults – Flyer</title>
<link href="https://fonts.googleapis.com/css2?family=Space+Grotesk:wght@400;500;600;700&family=Inter:ital,wght@0,400;0,700;1,400&display=swap" rel="stylesheet">
<style>
:root{
  --blue:#3a57fc;
  --ink:#111318;
  --muted:#3a3d44;
  --paper:#f3f4f7;
  --grid:rgba(20,30,60,0.045);
  --card:#ffffff;
  --line:#c9ccd4;
  --red:#ee3a30;
  --soft:#ececef;
}
*{margin:0;padding:0;box-sizing:border-box}
html,body{width:848px;height:1200px;overflow:hidden}
body{
  position:relative;
  font-family:"Space Grotesk",sans-serif;
  color:var(--ink);
  background-color:var(--paper);
  background-image:
    linear-gradient(var(--grid) 1px,transparent 1px),
    linear-gradient(90deg,var(--grid) 1px,transparent 1px);
  background-size:44px 44px;
}
.abs{position:absolute}
.hero-band,.hero-photo{position:absolute;left:0;top:0;width:848px;height:600px}
.brand{left:32px;top:87px;display:flex;align-items:center;gap:10px}
.brand-mark{width:37px;height:33px;background:var(--ink);border-radius:3px}
.brand-name{font-size:28px;font-weight:700;letter-spacing:-0.3px;color:var(--ink)}
.hero-title{left:460px;top:80px;font-size:42px;font-weight:700;line-height:47px;color:#fff;letter-spacing:-0.2px}
.hero-sub{left:465px;top:186px;width:360px;font-size:16px;font-weight:500;line-height:24px;color:#fff}
.intro-title{left:36px;top:160px;font-size:36px;font-weight:600;line-height:45px;letter-spacing:-0.2px}
.intro-body{left:36px;top:262px;width:390px;font-size:16.3px;font-weight:500;line-height:29px}
.section-title{font-size:24.5px;font-weight:600;line-height:28.5px}
.clients-title{left:37px;top:462px}
.hosting-title{left:287px;top:470px}
.review{left:28px;width:247px;height:84px;background:var(--card);border-radius:3px;box-shadow:0 2px 8px rgba(0,0,0,0.05)}
.avatar{position:absolute;left:17px;top:14px;width:37px;height:37px;border-radius:50%;background:var(--red);color:#fff;font-family:Inter,sans-serif;font-weight:700;font-size:11px;display:flex;align-items:center;justify-content:center}
.review-text{position:absolute;left:64px;top:10px;width:176px;font-family:Inter,sans-serif;font-style:italic;font-size:8.3px;line-height:13.3px;color:#555}
.review-name{position:absolute;left:64px;top:54px;font-family:Inter,sans-serif;font-weight:700;font-size:9px;color:var(--ink)}
.review-date{position:absolute;left:64px;top:68px;font-family:Inter,sans-serif;font-size:4.6px;color:var(--ink)}
.feature{width:169px;height:136px;border:1px solid var(--line);border-radius:3px;text-align:center;padding:12px 10px 0}
.feature svg{width:26px;height:30px;stroke:var(--blue);fill:none;stroke-width:1.6;stroke-linecap:round;stroke-linejoin:round}
.feature h3{font-size:12.5px;font-weight:500;margin-top:12px}
.feature p{font-size:6.3px;line-height:11.6px;color:var(--muted);margin-top:6px}
.contact-title{left:43px;top:932px;font-size:24.5px;font-weight:600;line-height:33px}
.contact{top:1029px;height:71px;background:var(--card);border-radius:10px}
.contact-icon{position:absolute;left:11px;top:8px;width:56px;height:56px;border-radius:50%;background:var(--soft);display:flex;align-items:center;justify-content:center}
.contact-icon svg{width:32px;height:32px;stroke:var(--blue);fill:none;stroke-width:1.8;stroke-linecap:round;stroke-linejoin:round}
.contact-name{position:absolute;left:80px;top:10px;font-size:24px;font-weight:600;white-space:nowrap}
.contact-sub{position:absolute;left:80px;top:42px;font-size:10px;font-weight:500;white-space:nowrap}
.contact-email .contact-sub{font-size:9.5px}
</style>
</head>
<body>

<svg class="hero-band" viewBox="0 0 848 600" aria-hidden="true">
  <polygon points="0,0 848,0 848,594 727,464 610,465 296,28 0,28" fill="var(--blue)"/>
</svg>
<svg class="hero-photo" viewBox="0 0 848 600" role="img" aria-label="Photo of mining hardware racks with cables in teal light">
  <defs>
    <linearGradient id="photoTone" x1="0" y1="0" x2="1" y2="1">
      <stop offset="0" stop-color="#0b1a24"/>
      <stop offset="0.45" stop-color="#13495a"/>
      <stop offset="0.75" stop-color="#0e2f3c"/>
      <stop offset="1" stop-color="#05080c"/>
    </linearGradient>
  </defs>
  <polygon points="319,0 848,0 848,543 750,426 624,421" fill="url(#photoTone)"/>
</svg>

<div class="abs brand">
  <span class="brand-mark"></span>
  <span class="brand-name">Quillfern Vaults</span>
</div>

<h1 class="abs hero-title">Transform Mining<br>With Cohosting</h1>
<p class="abs hero-sub">Miners deserve the best - choose the hosting company that delivers excellence!</p>

<h2 class="abs intro-title">Real Solutions For<br>Real Applications</h2>
<p class="abs intro-body">Quillfern Vaults has committed to leveraging cutting-edge technology, state-of-the-art facilities, and strategic partnerships to deliver exceptional solutions tailored for real-world applications in the cryptocurrency space.</p>

<h2 class="abs section-title clients-title">Our Clients’<br>Experiences<br>Speak Volumes</h2>
<h2 class="abs section-title hosting-title">Hosting Tailored To<br>Your Needs</h2>

<div class="abs review" style="top:586px">
  <div class="avatar">J</div>
  <p class="review-text">Excellent products, great communication and customer support. Would not hesitate to do business with again in the future.</p>
  <div class="review-name">rtovanek</div>
  <div class="review-date">Date of experience: February 03, 2024</div>
</div>
<div class="abs review" style="top:686px">
  <div class="avatar">J</div>
  <p class="review-text">Excellent products, great communication and customer support. Would not hesitate to do business with again in the future.</p>
  <div class="review-name">rtovanek</div>
  <div class="review-date">Date of experience: February 03, 2024</div>
</div>
<div class="abs review" style="top:785px">
  <div class="avatar">J</div>
  <p class="review-text">Excellent products, great communication and customer support. Would not hesitate to do business with again in the future.</p>
  <div class="review-name">rtovanek</div>
  <div class="review-date">Date of experience: February 03, 2024</div>
</div>

<div class="abs feature" style="left:288px;top:586px">
  <svg viewBox="0 0 26 30"><path d="M15 2 L4 17 H12 L10 28 L22 12 H14 Z"/></svg>
  <h3>99.45% Uptime</h3>
  <p>We boast an impressive uptime of 99.45% on average, ensuring consistent availability and reliability for users.</p>
</div>
<div class="abs feature" style="left:473px;top:586px">
  <svg viewBox="0 0 26 30"><rect x="3" y="3" width="16" height="22" rx="1.5"/><path d="M6 9h8M6 14h6M6 19h4"/><path d="M16 17l5-2 4 2v5c0 3-4 5-4 5s-5-2-5-5z"/></svg>
  <h3>Advanced Security</h3>
  <p>Employing advanced security measures for protection against potential threats and unauthorized access.</p>
</div>
<div class="abs feature" style="left:655px;top:586px">
  <svg viewBox="0 0 26 30"><rect x="2" y="21" width="22" height="6"/><rect x="6" y="12" width="10" height="9"/><rect x="17" y="4" width="6" height="6"/><path d="M11 12v9"/></svg>
  <h3>Large Facility Capacity</h3>
  <p>Our 4MW facility capacity underscores the infrastructure’s ability to accommodate high-energy demands.</p>
</div>
<div class="abs feature" style="left:288px;top:739px">
  <svg viewBox="0 0 26 30"><path d="M4 16v-3a9 9 0 0 1 18 0v3"/><rect x="2" y="15" width="4" height="7" rx="2"/><rect x="20" y="15" width="4" height="7" rx="2"/><path d="M22 22c0 3-3 4-7 4"/><circle cx="13" cy="26" r="2"/></svg>
  <h3>Expert Support</h3>
  <p>Benefit from expert support, ensuring assistance and guidance to optimize equipment and resolve issues effectively.</p>
</div>
<div class="abs feature" style="left:473px;top:739px">
  <svg viewBox="0 0 26 30"><circle cx="13" cy="15" r="10"/><path d="M9 19l3-6 7-5-3 8-6 4z"/></svg>
  <h3>Metered Usage</h3>
  <p>We exclusively bill you based on your usage, without exceptions! Leveraging state-of-the-art metering.</p>
</div>
<div class="abs feature" style="left:655px;top:739px">
  <svg viewBox="0 0 26 30"><circle cx="15" cy="8" r="5"/><path d="M12 12L3 24l2 2 3-2 1 2 2-3"/><rect x="18" y="17" width="6" height="7" rx="1"/></svg>
  <h3>Large Facility Capacity</h3>
  <p>Effectively command your operations with a comprehensive, full-spectrum control system - you got the keys.</p>
</div>

<h2 class="abs contact-title">Have Questions? Contact Us<br>For Expert Advice</h2>

<div class="abs contact" style="left:39px;width:210px">
  <div class="contact-icon"><svg viewBox="0 0 32 32"><path d="M18 6H6v15h5l-3 5"/><path d="M26 15v6H14"/><path d="M20 6h6v6M26 6l-8 8"/></svg></div>
  <div class="contact-name">Chat Us</div>
  <div class="contact-sub">Live Chat</div>
</div>
<div class="abs contact contact-email" style="left:271px;width:240px">
  <div class="contact-icon"><svg viewBox="0 0 32 32"><rect x="4" y="8" width="24" height="17" rx="1"/><path d="M4 9l12 9 12-9"/></svg></div>
  <div class="contact-name">Email Us</div>
  <div class="contact-sub">hello@quillfernvaults.example</div>
</div>
<div class="abs contact" style="left:531px;width:277px">
  <div class="contact-icon"><svg viewBox="0 0 32 32"><path d="M8 5l4 0 2 6-3 2c1 3 4 6 7 7l2-3 6 2v4c0 1-1 2-2 2C13 25 6 18 6 7c0-1 1-2 2-2z"/><path d="M19 5a8 8 0 0 1 8 8M19 9a4 4 0 0 1 4 4"/></svg></div>
  <div class="contact-name">Schedule 1-On-1</div>
  <div class="contact-sub">Interact With Us</div>
</div>

</body>
</html>
```